Bed Company needs business card

Hello, we are a bed company that makes specialized magnets for beds. We are an alternative healing company. I need a modern and upscale business card. Please incorporate my logo for the card.

Accepted file formats are AI, EPS, and Press-Ready PDFS.

Please include all fonts or convert them to outlines regardless of file type.

If you are designing the card in Photoshop the file Must be 1200dpi.

I am open to anything for the business card.  I really like all of your designs and if you want to change the color of the logo, you can.  I will be making the final selection by Friday.  Thank You for all of your designs.  Feel Free to submit different color logos if you want.  

Reason: I will make a decision Final on Friday April 20th. 2012. Good Luck and Thank you all for the designs.

Target Market(s)

My target Market is people, who are looking for alternative healing.

Industry/Entity Type

Business

Requirements
Must have
• My logo must be incorporated. The front card must have

Name
Job Title

Address
Work
Cell
Fax
email
web

Just put in fake info for the card.

The back of the card. I want the logo on the back with color. I just want it to look modern and cool.

```html
<!DOCTYPE html>
<html lang="en">
<head>
<meta charset="utf-8">
<title>Fernwell Health — Business Card</title>
<link href="https://fonts.googleapis.com/css2?family=Open+Sans:wght@400;700&display=swap" rel="stylesheet">
<style>
  :root {
    --backdrop: #d2d2d2;
    --card-white: #ffffff;
    --green-light: #52b848;
    --green-mid: #46a843;
    --green-dark: #1d7433;
    --ink: #444444;
    --ink-soft: #333333;
    --shadow: rgba(0, 0, 0, 0.28);
  }
  * { margin: 0; padding: 0; box-sizing: border-box; }
  html, body {
    width: 1200px;
    height: 900px;
    overflow: hidden;
  }
  body {
    background: var(--backdrop);
    font-family: "Open Sans", Arial, sans-serif;
    position: relative;
  }
  .card {
    position: absolute;
    top: 291px;
    width: 508px;
    height: 318px;
    box-shadow: 3px 4px 5px var(--shadow);
    overflow: hidden;
  }
  .card--front { left: 74px; background: var(--card-white); }
  .card--back {
    left: 620px;
    background: linear-gradient(to bottom, var(--green-light) 0%, var(--green-light) 45%, var(--green-mid) 70%, var(--green-dark) 100%);
  }
  .front-band {
    position: absolute;
    inset: 0;
    width: 508px;
    height: 318px;
  }
  .brand {
    position: absolute;
    display: flex;
    align-items: center;
    font-weight: 700;
    white-space: nowrap;
  }
  .brand__square {
    transform: rotate(45deg);
    flex: none;
  }
  .brand--front {
    left: 33px;
    top: 58px;
    color: var(--green-dark);
    font-size: 15px;
    gap: 9px;
  }
  .brand--front .brand__square {
    width: 20px;
    height: 20px;
    background: var(--green-dark);
  }
  .brand--back {
    left: 0;
    right: 0;
    top: 110px;
    justify-content: center;
    color: var(--card-white);
    font-size: 32px;
    gap: 22px;
  }
  .brand--back .brand__square {
    width: 48px;
    height: 48px;
    background: var(--card-white);
  }
  .holder {
    position: absolute;
    left: 270px;
    top: 58px;
    width: 206px;
    text-align: center;
  }
  .holder__name {
    font-size: 27px;
    font-weight: 400;
    color: var(--ink);
    line-height: 1.1;
  }
  .holder__title {
    font-size: 16px;
    color: var(--green-dark);
    margin-top: 2px;
  }
  .contact {
    position: absolute;
    left: 49px;
    top: 139px;
    font-size: 14.5px;
    color: var(--ink-soft);
    line-height: 20px;
  }
  .contact__row { display: flex; }
  .contact__label { width: 34px; }
  .contact__sep { width: 17px; }
  .online {
    position: absolute;
    left: 49px;
    top: 212px;
    font-size: 14.5px;
    color: var(--ink-soft);
    line-height: 21px;
  }
  .event {
    position: absolute;
    left: 46px;
    top: 287px;
    font-size: 12.5px;
    color: var(--ink-soft);
  }
</style>
</head>
<body>
  <section class="card card--front" aria-label="Business card front">
    <svg class="front-band" viewBox="0 0 508 318" aria-hidden="true">
      <defs>
        <linearGradient id="band-green" x1="0" y1="0" x2="0" y2="1">
          <stop offset="0" stop-color="#52b848"/>
          <stop offset="0.45" stop-color="#52b848"/>
          <stop offset="0.72" stop-color="#46a843"/>
          <stop offset="1" stop-color="#1d7433"/>
        </linearGradient>
      </defs>
      <polygon points="148,0 508,0 508,318 466,318" fill="url(#band-green)"/>
    </svg>

    <div class="brand brand--front">
      <span class="brand__square"></span>
      <span class="brand__name">Fernwell Health</span>
    </div>

    <div class="holder">
      <p class="holder__name">Daniel Reyes</p>
      <p class="holder__title">director</p>
    </div>

    <div class="contact">
      <p class="contact__row"><span class="contact__label">tel</span><span class="contact__sep">:</span><span>(999) 999 999</span></p>
      <p class="contact__row"><span class="contact__label">cell</span><span class="contact__sep">:</span><span>(999) 999 000</span></p>
      <p class="contact__row"><span class="contact__label">fax</span><span class="contact__sep">:</span><span>(999) 000 000</span></p>
    </div>

    <div class="online">
      <p>office@fernwellhealth.com</p>
      <p>www.fernwell-health.com</p>
    </div>

    <p class="event">May 12-15, 2013, Harbor Expo Hall, Riverton IL, Booth 2286</p>
  </section>

  <section class="card card--back" aria-label="Business card back">
    <div class="brand brand--back">
      <span class="brand__square"></span>
      <span class="brand__name">Fernwell Health</span>
    </div>
  </section>
</body>
</html>
```